Pastor's Lantern: How To Help Church Leaders Remain Strong In Their Callings.

I have created a 250-page book tentatively entitled, Pastor's Lantern, subtitle: Practical Help For Pastors And Leaders Facing The Daily Trials Of Ministry. The chapters are taken from my podcast of the same name on TuneVault and website: pastorslantern-example.com which will need updating soon. The purpose of the book is to provide practical solutions to pastors/leaders about everyday issues faced in ministry such as loneliness, financial challenges, a pastor's family problems, sexual temptation ...etc. You can get an idea of the topics from TuneVault.
Updates

As mentioned in the brief, I am looking for something that will communicate solutions. My podcast, Pastor's Lantern from which this material originates is all about practical help for local pastors in facing the challenges of daily ministry. The logo I sent was designed for concept purposes only. It does not need to be on the cover necessarily unless it feeds into the overall theme.

Target Market(s)

Pastors and Church Leaders in the Christian Faith

Industry/Entity Type

Religious

Font styles to use
Serif

Colors

Designer to choose colors to be used in the design.

Requirements
Must have
• Crisp copy and lines. People see covers for 3 seconds. If they are not drawn in by complicated themes, I have failed. Many of the designs so far do not address the topic of the book in a way that impacts. This is about a toolbox or book that provides solutions to their everyday challenges. If it doesn't somehow point to tools, it should instead point to getting solutions.
Nice to have
• I have included a copy of my current logo. If you can incorporate it, fine. If you have a better idea, I am open to that and would be interested in contributing more if the logo is superior. The logo is not essential to either front or back cover..
Should not have
• Simplistic religious themes from often used pics. I will peruse other book covers in my genre. If I find the same pic used, it disqualifies the design immediately no matter how much I like it. Target audience is ministers. Simplistic cross designs have gotten less votes so far in polling. I want to grab attention with a compelling picture that communicates solutions.

```html
<!DOCTYPE html>
<html lang="en">
<head>
<meta charset="utf-8">
<title>Pastor's Lantern – Book Cover</title>
<link rel="stylesheet" href="https://fonts.googleapis.com/css2?family=Anton&family=Cinzel:wght@400;500&display=swap">
<style>
  :root {
    --stage: #1c1c1c;
    --band: #ffffff;
    --author-ink: #2b2b2b;
    --title-ink: #f3ece6;
    --title-soft: #e6d2c2;
    --sub-ink: #fff4ea;
    --sky-top: #5b4d48;
    --sky-mid: #8a4a34;
    --glow: #e0441a;
    --horizon: #f37d1c;
    --sea: #d03a18;
    --sea-deep: #3a1710;
  }
  * { margin: 0; padding: 0; box-sizing: border-box; }
  html, body { width: 1200px; height: 905px; overflow: hidden; background: var(--stage); }
  .canvas { position: relative; width: 1200px; height: 905px; display: flex; align-items: center; justify-content: center; }
  .cover { position: relative; width: 540px; height: 850px; background: var(--sea-deep); overflow: hidden; box-shadow: 0 10px 40px rgba(0,0,0,.6); }
  .author-band { position: absolute; top: 0; left: 0; right: 0; height: 78px; background: var(--band); display: flex; align-items: center; justify-content: center; }
  .author { font-family: "Cinzel", serif; font-weight: 500; font-size: 31px; letter-spacing: 5px; color: var(--author-ink); }
  .cover-photo { position: absolute; top: 78px; left: 0; right: 0; bottom: 0;
    background: linear-gradient(180deg, var(--sky-top) 0%, var(--sky-mid) 28%, var(--glow) 50%, var(--horizon) 64%, var(--sea) 72%, #b32a14 86%, var(--sea-deep) 100%); }
  .title-block { position: absolute; top: 232px; left: 0; right: 0; text-align: center; font-weight: 400; }
  .title-top { display: block; font-family: "Anton", sans-serif; font-size: 46px; letter-spacing: 22px; padding-left: 22px; color: var(--title-soft); line-height: 1; }
  .title-main { display: block; font-family: "Anton", sans-serif; font-size: 128px; letter-spacing: 2px; color: var(--title-ink); line-height: 1.05; margin-top: 8px; }
  .subtitle { position: absolute; top: 455px; left: 30px; right: 20px; text-align: center; font-family: "Cinzel", serif; font-size: 19px; line-height: 1.05; color: var(--sub-ink); transform: rotate(2.5deg); }
  .imprint { position: absolute; top: 752px; left: 0; right: 0; display: flex; justify-content: center; align-items: center; gap: 6px; font-family: "Cinzel", serif; font-weight: 500; font-size: 17px; color: var(--sub-ink); }
  .imprint-mark { width: 9px; height: 9px; background: var(--sub-ink); }
</style>
</head>
<body>
<main class="canvas">
  <article class="cover">
    <header class="author-band"><p class="author">DANA R. WHITFIELD</p></header>
    <div class="cover-photo" role="img" aria-label="Photograph of a red-orange sunset over a calm sea, with a low island on the horizon and a small sailboat reflected in the water"></div>
    <h1 class="title-block">
      <span class="title-top">PASTOR'S</span>
      <span class="title-main">LANTERN</span>
    </h1>
    <p class="subtitle">PRACTICAL HELP FOR PASTORS AND LEADERS<br>FACING THE DAILY TRIALS OF MINISTRY</p>
    <footer class="imprint"><span class="imprint-mark"></span><span>Pastor's Lantern</span></footer>
  </article>
</main>
</body>
</html>
```